Kelvor Engineers: Why you should hire us keepsake

New design. Open to plastic cards. We are an engineering firm that designs cell phone towers and commercial buildings. Please check out our website www.kelvorstruct.com for more details. We want people to remember our card and for it to be useful if possible. We want the same look and feel on these cards to be translated to other marketing material we may need such as brochures.

Target Market(s)

Architects, Developers and Telecommunication Carriers

Industry/Entity Type

Engineering

Contact Information for Business Card

Card with our company colors, logo, and innovative design with elements related to our industry.

Font styles to use
Sans Serif

Colors
9bcb3c
abd036
0255a3

Requirements
Must have
• Sleek and hip design
Nice to have
• Bright lime green and navy coloring that pops with an innovative design.
Should not have
• A basic and boring design

```html
<!DOCTYPE html>
<html lang="en">
<head>
<meta charset="utf-8">
<title>Kelvor Engineers – Business Card</title>
<link href="https://fonts.googleapis.com/css2?family=Open+Sans:wght@400;600;700;800&display=swap" rel="stylesheet">
<style>
  :root {
    --bg: #d9d9db;
    --card: #ffffff;
    --lime: #21f021;
    --navy: #0f2f5f;
    --text-navy: #14305e;
    --white: #ffffff;
  }
  * { margin: 0; padding: 0; box-sizing: border-box; }
  html, body {
    width: 1200px; height: 1000px; overflow: hidden;
    background: var(--bg);
    font-family: "Open Sans", Arial, sans-serif;
  }
  .canvas { position: relative; width: 1200px; height: 1000px; }
  .card {
    position: absolute; left: 270px; width: 662px; height: 380px;
    background: var(--card); border-radius: 22px; overflow: hidden;
    box-shadow: 0 4px 10px rgba(0,0,0,.25);
  }
  .card--front { top: 77px; }
  .card--back { top: 520px; }

  .wordmark {
    position: absolute; font-weight: 800; color: var(--lime);
    letter-spacing: -2px; line-height: 1;
  }
  .card--front .wordmark {
    left: 0; right: 0; top: 128px; text-align: center; font-size: 118px;
  }
  .offices {
    position: absolute; left: 0; right: 0; top: 325px;
    text-align: center; font-size: 19px; color: var(--text-navy);
    letter-spacing: .3px;
  }
  .offices .sep { color: var(--lime); margin: 0 9px; }

  .card--back .wordmark { left: 22px; top: 30px; font-size: 92px; }
  .tagline {
    position: absolute; right: 30px; top: 34px;
    font-size: 18px; font-weight: 700; color: var(--text-navy);
  }
  .swoosh { position: absolute; inset: 0; }
  .contact { position: absolute; right: 30px; top: 232px; text-align: right; color: var(--white); }
  .contact .name { font-size: 18px; font-weight: 700; margin-bottom: 14px; }
  .contact ul { list-style: none; font-size: 13.5px; line-height: 19.5px; }
  .contact li { display: flex; justify-content: flex-end; align-items: center; gap: 5px; }
  .contact svg { width: 11px; height: 11px; fill: var(--lime); }
</style>
</head>
<body>
<div class="canvas">

  <section class="card card--front">
    <div class="wordmark">Kelvor</div>
    <p class="offices">DENVER<span class="sep">|</span>RALEIGH<span class="sep">|</span>PHOENIX<span class="sep">|</span>SALT LAKE CITY</p>
  </section>

  <section class="card card--back">
    <div class="wordmark">Kelvor</div>
    <p class="tagline">Multi-discipline engineering</p>

    <svg class="swoosh" viewBox="0 0 662 380" preserveAspectRatio="none" aria-hidden="true">
      <path d="M0,270 C140,320 260,250 380,180 C480,125 580,112 662,118 L662,132 C575,128 485,145 390,195 C270,262 140,318 0,292 Z" fill="var(--lime)"/>
      <path d="M0,300 C150,350 290,280 410,210 C510,158 590,146 662,150 L662,380 L0,380 Z" fill="var(--navy)"/>
      <path d="M0,332 C150,372 290,310 400,240 C450,210 490,195 520,188 C490,200 455,218 405,250 C290,322 150,382 0,342 Z" fill="var(--white)"/>
    </svg>

    <div class="contact">
      <p class="name">Dana Holloway Reese</p>
      <ul>
        <li>555.210.4832 <svg viewBox="0 0 12 12"><path d="M2 1l2.5 0 1 3-1.5 1c.6 1.4 1.6 2.4 3 3l1-1.5 3 1V11c-5 .5-9.5-4-9-10z"/></svg></li>
        <li>555.640.1937 <svg viewBox="0 0 12 12"><path d="M3 0h6a1 1 0 011 1v10a1 1 0 01-1 1H3a1 1 0 01-1-1V1a1 1 0 011-1zm.5 1.5v8h5v-8z"/></svg></li>
        <li>dreese@kelvorstruct.com <svg viewBox="0 0 12 12"><path d="M0 2h12v8H0zm1 1l5 4 5-4z"/></svg></li>
        <li>www.kelvorstruct.com <svg viewBox="0 0 12 12"><circle cx="6" cy="6" r="6"/></svg></li>
      </ul>
    </div>
  </section>

</div>
</body>
</html>
```